Redesign of business card for Cedar Ridge Mechanical

We are looking for a new design for our business cards for Cedar Ridge Mechanical. We are a plumbing & HVAC construction company, operating on the West Coast of Canada and USA. Logo attached.
Industry/Entity Type
Construction - Plumbing & HVAC
Contact Information for Business Card
Name, address, phone numbers, email, website address
Look and feel
Each slider illustrates characteristics of the customer's brand and the style your logo design should communicate.

```html
<!DOCTYPE html>
<html lang="en">
<head>
<meta charset="utf-8">
<title>Cedar Ridge Mechanical – Business Card</title>
<link href="https://fonts.googleapis.com/css2?family=Montserrat:wght@400;700&display=swap" rel="stylesheet">
<style>
  :root {
    --backdrop: #d0d0d0;
    --card: #f3f3f1;
    --ink: #111111;
    --ink-soft: #6e6e6e;
    --rule: #c9c9c6;
  }
  html, body {
    margin: 0;
    width: 1200px;
    height: 1051px;
    overflow: hidden;
    background: var(--backdrop);
    font-family: "Montserrat", sans-serif;
  }
  .stage { position: relative; width: 1200px; height: 1051px; }
  .card {
    position: absolute;
    width: 560px;
    height: 320px;
    background: var(--card);
    box-shadow: 0 14px 30px rgba(0,0,0,0.14);
    border-bottom: 4px solid var(--ink);
    box-sizing: border-box;
  }
  .card--back { left: 560px; top: 170px; }
  .card--front { left: 80px; top: 560px; }

  .brand {
    position: absolute; inset: 0;
    display: flex; align-items: center; justify-content: center; gap: 18px;
  }
  .brand__mark { width: 26px; height: 26px; background: var(--ink); }
  .brand__name {
    font-weight: 700; font-size: 28px; letter-spacing: 2px;
    text-transform: uppercase; color: var(--ink);
  }

  .identity {
    position: absolute; left: 60px; top: 110px; width: 190px; text-align: right;
  }
  .identity__name { font-weight: 700; font-size: 21px; color: var(--ink); letter-spacing: 0.5px; }
  .identity__title { font-weight: 400; font-size: 14px; color: var(--ink-soft); margin-top: 4px; }
  .divider {
    position: absolute; left: 278px; top: 100px; width: 1px; height: 80px; background: var(--rule);
  }
  .contacts {
    position: absolute; left: 300px; top: 100px; margin: 0; padding: 0; list-style: none;
  }
  .contacts li {
    display: flex; align-items: center; gap: 8px;
    font-size: 14px; color: var(--ink-soft); line-height: 21px;
  }
  .contacts svg { width: 11px; height: 11px; fill: var(--ink); flex: none; }
  .contacts .note { color: var(--ink); font-size: 12px; }
  .address {
    position: absolute; left: 0; right: 0; bottom: 44px;
    text-align: center; font-size: 13px; color: var(--ink-soft); letter-spacing: 0.3px;
  }
</style>
</head>
<body>
<main class="stage">
  <section class="card card--back">
    <div class="brand">
      <span class="brand__mark"></span>
      <span class="brand__name">Cedar Ridge Mechanical</span>
    </div>
  </section>

  <section class="card card--front">
    <div class="identity">
      <div class="identity__name">MARCUS DELANEY</div>
      <div class="identity__title">President</div>
    </div>
    <div class="divider"></div>
    <ul class="contacts">
      <li><svg viewBox="0 0 12 12"><path d="M2.5 0.5 L4.5 0.5 L5.2 3.2 L3.8 4.3 C4.5 5.8 6.2 7.5 7.7 8.2 L8.8 6.8 L11.5 7.5 L11.5 9.5 C11.5 10.6 10.6 11.5 9.5 11.5 C4.8 11.5 0.5 7.2 0.5 2.5 C0.5 1.4 1.4 0.5 2.5 0.5Z"/></svg>1-866-555-0142 <span class="note">Toll Free</span></li>
      <li><svg viewBox="0 0 12 12"><path d="M2.5 0.5 L4.5 0.5 L5.2 3.2 L3.8 4.3 C4.5 5.8 6.2 7.5 7.7 8.2 L8.8 6.8 L11.5 7.5 L11.5 9.5 C11.5 10.6 10.6 11.5 9.5 11.5 C4.8 11.5 0.5 7.2 0.5 2.5 C0.5 1.4 1.4 0.5 2.5 0.5Z"/></svg>213-555-0178</li>
      <li><svg viewBox="0 0 12 12"><path d="M0.5 2 H11.5 V10 H0.5Z M1 2.5 L6 6.5 L11 2.5" stroke="#f3f3f1" stroke-width="0.9"/></svg>info@cedarridgemech.com</li>
      <li><svg viewBox="0 0 12 12"><circle cx="6" cy="6" r="5.5"/><path d="M0.5 6 H11.5 M6 0.5 C3.5 3 3.5 9 6 11.5 M6 0.5 C8.5 3 8.5 9 6 11.5" stroke="#f3f3f1" stroke-width="0.8" fill="none"/></svg>www.cedarridgemech.com</li>
    </ul>
    <div class="address">4120 Harbor Lane, Suite 200, Fairview, CA 92640</div>
  </section>
</main>
</body>
</html>
```